Redesign of Form/Document Navigation Page

I need a redesign of our document and navigation bar on the left. We want the same navigation bar layout/setup but want the buttons and typography to be simple and matching all over. The form needs to be aesthetically pleasing and fit within the page.

1st attachment is our Direct Deposit and the second is the form continued.

```html
<!DOCTYPE html>
<html lang="en">
<head>
<meta charset="utf-8">
<title>Sentinel Patrol Services – Document</title>
<link href="https://fonts.googleapis.com/css2?family=Roboto+Slab:wght@300;400;700&family=Roboto:wght@400;500;700&family=Montserrat:wght@800&display=swap" rel="stylesheet">
<style>
  :root {
    --navy: #1c3f94;
    --gold: #fdb316;
    --page: #f3f3f5;
    --line: #dcdcdc;
    --text: #555;
    --muted: #777;
    --footer: #555555;
    --white: #ffffff;
  }
  * { box-sizing: border-box; margin: 0; padding: 0; }
  html, body { width: 1200px; height: 865px; overflow: hidden; }
  body { position: relative; background: var(--page); font-family: "Roboto Slab", serif; color: var(--text); }

  .site-header { position: absolute; left: 0; top: 0; width: 1200px; height: 88px; background: var(--white); border-bottom: 1px solid var(--line); }
  .brand { position: absolute; left: 25px; top: 18px; display: flex; align-items: center; gap: 10px; }
  .brand-mark { width: 40px; height: 46px; background: var(--navy); border-radius: 4px; }
  .brand-name { font-family: "Montserrat", sans-serif; font-weight: 800; font-size: 20px; line-height: 20px; color: var(--gold); text-transform: uppercase; letter-spacing: -0.3px; }
  .top-nav { position: absolute; right: 28px; top: 35px; display: flex; align-items: center; font-family: "Roboto", sans-serif; font-size: 12px; color: #666; }
  .top-nav span { margin: 0 10px; }
  .top-nav .divider { margin: 0 12px; }
  .power-btn { width: 28px; height: 24px; background: var(--navy); display: flex; align-items: center; justify-content: center; margin-left: 2px; }

  .back-tab { position: absolute; left: 25px; top: 94px; width: 119px; height: 30px; background: var(--navy); color: var(--white); font-family: "Roboto", sans-serif; font-weight: 700; font-size: 11px; line-height: 30px; padding-left: 11px; }
  .sidebar { position: absolute; left: 25px; top: 123px; width: 246px; height: 569px; background: var(--white); border: 1px solid var(--line); padding: 26px 0 0 16px; }
  .side-btn { display: flex; width: 196px; height: 46px; border-radius: 12px; margin-bottom: 31px; overflow: hidden; color: var(--white); font-weight: 700; font-size: 12px; text-transform: uppercase; }
  .side-btn.gold { background: var(--gold); }
  .side-btn.navy { background: var(--navy); }
  .side-btn .icon { width: 60px; flex: none; display: flex; align-items: center; justify-content: center; border-right: 1px solid rgba(255,255,255,.6); }
  .side-btn .label { display: flex; align-items: center; padding-left: 16px; line-height: 15px; }
  .side-btn .label.tight { padding-left: 5px; }

  .document { position: absolute; left: 286px; top: 124px; width: 885px; height: 642px; background: var(--white); border: 1px solid var(--line); }
  .scrollbar { position: absolute; right: 0; top: 0; width: 12px; height: 100%; background: #f1f1f1; border-left: 1px solid #e3e3e3; }
  .scrollbar .thumb { position: absolute; left: 1px; top: 67px; width: 9px; height: 286px; background: #dadada; border: 1px solid #c8c8c8; border-radius: 2px; }
  .doc-title { position: absolute; left: 21px; top: 18px; font-size: 19px; font-weight: 400; color: var(--navy); }
  .doc-intro { position: absolute; left: 22px; top: 60px; width: 832px; font-size: 11px; font-weight: 300; line-height: 20.3px; color: var(--muted); }
  .field-label { position: absolute; font-size: 12px; font-weight: 300; color: var(--text); }
  .field { position: absolute; background: var(--white); border: 1px solid #d6d6d6; border-radius: 3px; }
  .btn-accept { position: absolute; left: 21px; top: 314px; width: 175px; height: 48px; background: var(--gold); border-radius: 13px; color: var(--white); font-weight: 700; font-size: 13px; display: flex; align-items: center; justify-content: center; }
  .section-title { position: absolute; left: 21px; top: 403px; font-size: 18px; font-weight: 400; color: #555; }
  .btn-submit { position: absolute; left: 702px; top: 576px; width: 109px; height: 36px; background: var(--navy); border-radius: 2px; color: var(--white); font-weight: 700; font-size: 14px; display: flex; align-items: center; justify-content: center; }

  .site-footer { position: absolute; left: 0; top: 805px; width: 1200px; height: 60px; background: var(--footer); color: var(--white); font-family: "Roboto", sans-serif; font-size: 11px; }
  .site-footer .copy { position: absolute; left: 25px; top: 23px; }
  .site-footer .code { position: absolute; right: 28px; top: 28px; }
</style>
</head>
<body>
  <header class="site-header">
    <div class="brand">
      <div class="brand-mark"></div>
      <div class="brand-name">Sentinel<br>Patrol Services</div>
    </div>
    <nav class="top-nav">
      <span>HOME</span><span class="divider">|</span><span>HELP</span>
      <div class="power-btn">
        <svg width="12" height="12" viewBox="0 0 12 12" fill="none" stroke="#fff" stroke-width="1.6" stroke-linecap="round"><path d="M3.5 3.2A4 4 0 1 0 8.5 3.2"/><path d="M6 1v4.5"/></svg>
      </div>
    </nav>
  </header>

  <div class="back-tab">BACK TO PROFILE</div>

  <aside class="sidebar">
    <div class="side-btn gold">
      <div class="icon"><svg width="34" height="24" viewBox="0 0 34 24" fill="none" stroke="#fff" stroke-width="1.8"><rect x="5" y="6" width="26" height="14" rx="1"/><rect x="2" y="3" width="26" height="14" rx="1" fill="#fdb316"/><circle cx="15" cy="10" r="3.5"/><path d="M2 20h6M1 23h8"/></svg></div>
      <div class="label">Direct Deposit</div>
    </div>
    <div class="side-btn navy">
      <div class="icon"><svg width="32" height="30" viewBox="0 0 32 30" fill="#fff"><circle cx="18" cy="8" r="6"/><path d="M8 28c0-8 4-12 10-12s10 4 10 12z"/><path d="M3 22a5 5 0 0 1 9-2M12 24a5 5 0 0 1-9 2" stroke="#fff" stroke-width="2" fill="none"/></svg></div>
      <div class="label">Change W-4</div>
    </div>
    <div class="side-btn gold">
      <div class="icon"><svg width="34" height="24" viewBox="0 0 34 24" fill="none" stroke="#fff" stroke-width="2.6" stroke-linecap="round" stroke-linejoin="round"><path d="M9 5 3 12l6 7M25 5l6 7-6 7M20 3l-6 18"/></svg></div>
      <div class="label">Labour Code</div>
    </div>
    <div class="side-btn navy">
      <div class="icon"><svg width="34" height="26" viewBox="0 0 34 26" fill="#fff"><circle cx="10" cy="7" r="6"/><path d="M0 25c0-7 4-10 10-10s10 3 10 10z"/><rect x="20" y="4" width="13" height="3"/><rect x="22" y="11" width="11" height="3"/><rect x="22" y="18" width="11" height="3"/></svg></div>
      <div class="label">Personal Info</div>
    </div>
    <div class="side-btn gold">
      <div class="icon"><svg width="26" height="30" viewBox="0 0 26 30" fill="none" stroke="#fff" stroke-width="2"><rect x="2" y="4" width="22" height="25" rx="1"/><rect x="8" y="1" width="10" height="5" fill="#fdb316"/><path d="M6 12l2 2 3-3M6 20l2 2 3-3M14 13h6M14 21h6"/></svg></div>
      <div class="label tight">Appraisel &amp; Review</div>
    </div>
    <div class="side-btn navy">
      <div class="icon"><svg width="30" height="30" viewBox="0 0 30 30" fill="none" stroke="#fff" stroke-width="2.4"><path d="M20 4H3v23h23V11"/><path d="M10 20l2-6 13-13 4 4-13 13z" fill="#fff"/></svg></div>
      <div class="label">Write Up-Slip</div>
    </div>
    <div class="side-btn gold">
      <div class="icon"><svg width="34" height="32" viewBox="0 0 34 32" fill="#fff"><rect x="2" y="22" width="4" height="9"/><rect x="8" y="19" width="4" height="12"/><rect x="14" y="16" width="4" height="15"/><rect x="20" y="12" width="4" height="19"/><rect x="26" y="7" width="4" height="24"/><path d="M2 17 22 5l-2-3h11l-4 10-2-3L4 20z"/></svg></div>
      <div class="label">Employee<br>Performance</div>
    </div>
  </aside>

  <main class="document">
    <div class="scrollbar"><div class="thumb"></div></div>
    <h1 class="doc-title">IMPORTANT! Please read and sign before completing and submitting.</h1>
    <p class="doc-intro">There are many variations of passages of Lorem Ipsum available, but the majority have suffered alteration in some form, by injected humour, or randomised words which don't look even slightly believable. If you are going to use a passage of Lorem Ipsum, you need to be sure there isn't anything embarrassing hidden in the middle of text. All the Lorem Ipsum generators on the Internet tend to repeat predefined chunks as necessary, making this the first true generator on the Internet. It uses a dictionary of over 200 Latin words, combined with a handful of model sentence structures, to generate Lorem Ipsum.</p>

    <label class="field-label" style="left:22px;top:168px">Employee Name:</label>
    <div class="field" style="left:21px;top:181px;width:255px;height:38px"></div>
    <label class="field-label" style="left:660px;top:168px">Sign Date &nbsp;:</label>
    <div class="field" style="left:659px;top:181px;width:188px;height:32px"></div>
    <label class="field-label" style="left:22px;top:238px">Employee Signature</label>
    <div class="field" style="left:21px;top:251px;width:255px;height:45px"></div>
    <div class="btn-accept">ACCEPT DOCUMENT</div>

    <h2 class="section-title">Only Payroll Manager Signs Below</h2>
    <label class="field-label" style="left:22px;top:449px">Company Name:</label>
    <div class="field" style="left:21px;top:462px;width:315px;height:32px"></div>
    <label class="field-label" style="left:392px;top:449px">Comments:</label>
    <div class="field" style="left:392px;top:462px;width:419px;height:100px"></div>
    <label class="field-label" style="left:22px;top:518px">Employee File Number:</label>
    <div class="field" style="left:21px;top:531px;width:315px;height:32px"></div>
    <div class="btn-submit">SUBMIT</div>
  </main>

  <footer class="site-footer">
    <div class="copy">Copyright © 2016 &nbsp;SPS.All Rights Reserved.</div>
    <div class="code">C19</div>
  </footer>
</body>
</html>
```